New Business Card Design Project

Use the flyer uploaded and website www.brightoakbuilders.com for inspiration.
List Our Services on Backside of business cards
Marcus Delling
Harborline Builders Inc.
Licensed General Contractors
858-471-6093

Contact Information for Business Card

Use the flyer uploaded and website www.brightoakbuilders.com for inspiration. List Our Services on Backside of business cards Marcus Delling Harborline Builders Inc. Licensed General Contractors 858-471-6093

```html
<!DOCTYPE html>
<html lang="en">
<head>
<meta charset="utf-8">
<title>Harborline Builders – Business Card</title>
<link href="https://fonts.googleapis.com/css2?family=Marcellus&family=Arimo:wght@400&display=swap" rel="stylesheet">
<style>
  :root {
    --page: #e6e6e6;
    --card-light: #f1f1f2;
    --card-back: #ffffff;
    --charcoal: #323232;
    --stripe: #a9a7a8;
    --ink: #2a2a2a;
    --ink-soft: #333333;
    --on-dark: #f2f2f2;
  }
  html, body {
    margin: 0;
    width: 1200px;
    height: 1040px;
    overflow: hidden;
    background: var(--page);
  }
  .canvas {
    position: relative;
    width: 1200px;
    height: 1040px;
  }
  .card {
    position: absolute;
    left: 282px;
    width: 644px;
    height: 366px;
    border-radius: 16px;
    overflow: hidden;
  }
  .card--front { top: 130px; background: var(--card-light); }
  .card--back  { top: 568px; background: var(--card-back); }

  .front-shapes { position: absolute; inset: 0; }

  .brand-name {
    position: absolute;
    font-family: "Marcellus", serif;
    letter-spacing: 1px;
    white-space: nowrap;
    text-align: center;
  }
  .card--front .brand-name {
    left: 0; width: 320px;
    top: 196px;
    font-size: 21px;
    color: var(--on-dark);
  }
  .card--back .brand-name {
    left: 0; right: 0;
    top: 104px;
    font-size: 36px;
    color: var(--ink);
  }

  .contact {
    position: absolute;
    right: 29px;
    top: 92px;
    text-align: right;
    color: var(--ink-soft);
    font-family: "Arimo", sans-serif;
  }
  .contact__name {
    font-family: "Marcellus", serif;
    font-weight: 400;
    font-size: 20px;
    letter-spacing: 0.5px;
    white-space: nowrap;
    color: var(--ink);
    margin: 0 0 24px;
    text-transform: uppercase;
  }
  .contact__line {
    display: flex;
    justify-content: flex-end;
    align-items: center;
    gap: 8px;
    font-size: 15.5px;
    line-height: 20px;
    white-space: nowrap;
  }
  .contact__line svg { width: 13px; height: 13px; fill: var(--ink); }
  .contact__company {
    margin-top: 20px;
    font-size: 15.5px;
    line-height: 20px;
    white-space: nowrap;
  }

  .services {
    position: absolute;
    left: 0; right: 0;
    top: 212px;
    text-align: center;
    color: var(--ink-soft);
    font-family: "Arimo", sans-serif;
  }
  .services__title {
    font-family: "Marcellus", serif;
    font-weight: 400;
    font-size: 20px;
    letter-spacing: 3px;
    color: var(--ink);
    margin: 0 0 8px;
  }
  .services__row {
    font-size: 15.5px;
    line-height: 23px;
    white-space: nowrap;
  }
  .services__sep {
    display: inline-block;
    width: 7px; height: 7px;
    background: var(--ink);
    margin: 0 9px;
    vertical-align: 2px;
  }
</style>
</head>
<body>
<div class="canvas">

  <section class="card card--front">
    <svg class="front-shapes" viewBox="0 0 644 366" aria-hidden="true">
      <polygon points="0,0 497,0 237,366 0,366" fill="var(--charcoal)"/>
      <polygon points="490,6 219,366 191,366" fill="var(--stripe)"/>
    </svg>
    <div class="brand-name">HARBORLINE BUILDERS</div>

    <div class="contact">
      <h1 class="contact__name">Marcus Delling</h1>
      <div class="contact__line">858-471-6093
        <svg viewBox="0 0 24 24"><path d="M6.6 10.8a15.1 15.1 0 0 0 6.6 6.6l2.2-2.2a1 1 0 0 1 1-.25 11.4 11.4 0 0 0 3.6.57 1 1 0 0 1 1 1V20a1 1 0 0 1-1 1A17 17 0 0 1 3 4a1 1 0 0 1 1-1h3.5a1 1 0 0 1 1 1c0 1.25.2 2.45.57 3.57a1 1 0 0 1-.25 1z"/></svg>
      </div>
      <div class="contact__line">info@brightoakbuilders.com
        <svg viewBox="0 0 24 24"><path d="M2 6l10 7 10-7V5H2zM2 8v11h20V8l-10 7z"/></svg>
      </div>
      <div class="contact__line">www.brightoakbuilders.com
        <svg viewBox="0 0 24 24"><circle cx="12" cy="12" r="10"/><path d="M8 6c2 1 1 3 3 4s-1 3 1 5M15 17c0-2 2-2 3-3" stroke="#fff" stroke-width="1.6" fill="none"/></svg>
      </div>
      <div class="contact__company">Harborline Builders Inc.<br>Licensed General Contractors</div>
    </div>
  </section>

  <section class="card card--back">
    <div class="brand-name">HARBORLINE BUILDERS</div>
    <div class="services">
      <h2 class="services__title">SERVICES</h2>
      <div class="services__row">Remodel : Kitchen &amp; Bath<span class="services__sep"></span>Painting : Interior &amp; Exterior</div>
      <div class="services__row">Flooring : Carpet, Vinyl, Wood<span class="services__sep"></span>Window &amp; Door Replacement</div>
      <div class="services__row">Plumbing : Repairs &amp; Upgrades<span class="services__sep"></span>Energy- Efficient Upgrades</div>
      <div class="services__row">Deck &amp; Pation Construction<span class="services__sep"></span>Water &amp; Mold Damage<span class="services__sep"></span>Garage Renovation</div>
    </div>
  </section>

</div>
</body>
</html>
```